Consultancy Business Card Design

We need a business card design for a new company based in singapore called KestrelOak. KestrelOak a boutique consultancy firm offering broad-based business solutions, from conception to re-invention, for ventures from new start-ups to long-running traditional businesses.
Its 2 main divisions (Food & Beverage Operations and Construction & Project Management) have access to a wide range of networks, knowledge bases, and resources to service its clients across numerous diverse sectors. This includes, and is not limited to, construction, F&B, and retail.
We are a company that combines the ambition, boldness and energy of one in the 20s with the dedication, level-headedness and dependability of one entering its 30s. Bridging the experiences of the old with ideals of the young, we draw on the positives of both to create a unique synergy.
We hope to see designs that fits our company profile.
Industry/Entity Type
Boutique
Contact Information for Business Card
KestrelOak(Company Name)
Marcus Thiel (Name)
Principle Consultant (Title)
F&B and Hospitality (Division)
(+65) 8043 5617 (Contact no.)
marcus@kestreloak.com.sg (Email)
Colors
Designer to choose colors to be used in the design.

```html
<!DOCTYPE html>
<html lang="en">
<head>
<meta charset="utf-8">
<title>KestrelOak — Business Card</title>
<link href="https://fonts.googleapis.com/css2?family=Montserrat:wght@400;500;600&display=swap" rel="stylesheet">
<style>
  :root {
    --backdrop: #2b2b2b;
    --card: #161616;
    --card-edge: #202020;
    --accent: #e8343a;
    --logo-panel: #f3f3f3;
    --logo-ink: #2a2a2a;
    --text-light: #d8d8d8;
    --text-muted: #b9b9b9;
    --icon-line: #cfcfcf;
  }
  * { box-sizing: border-box; margin: 0; padding: 0; }
  html, body {
    width: 1200px; height: 900px; overflow: hidden;
    background: var(--backdrop);
    font-family: "Montserrat", sans-serif;
  }
  .stage {
    width: 1200px; height: 900px;
    display: flex; flex-direction: column;
    align-items: center; justify-content: center; gap: 44px;
  }
  .card {
    position: relative;
    width: 680px; height: 388px;
    background: radial-gradient(ellipse at 50% 40%, var(--card-edge), var(--card) 75%);
    box-shadow: 0 14px 30px rgba(0,0,0,0.45);
    overflow: hidden;
  }
  .card__stripe {
    position: absolute; left: 0; right: 0; bottom: 0;
    height: 14px; background: var(--accent);
  }
  .logo-panel {
    position: absolute; left: 50%;
    transform: translateX(-50%);
    width: 290px; height: 74px;
    background: var(--logo-panel);
    display: flex; align-items: center; justify-content: center;
  }
  .card--front .logo-panel { top: 92px; }
  .card--back .logo-panel { top: 150px; }
  .logo-panel__name {
    font-weight: 500; font-size: 40px; letter-spacing: -0.5px;
    color: var(--logo-ink);
  }
  .contact {
    position: absolute; top: 246px;
    display: flex; flex-direction: column; align-items: flex-start; gap: 10px;
  }
  .contact--person { left: 42px; }
  .contact--phone { left: 262px; }
  .contact--email { left: 420px; }
  .contact__icon { width: 26px; height: 26px; display: block; }
  .contact__lines { font-size: 12.5px; line-height: 1.45; color: var(--text-light); }
  .contact__role { color: var(--accent); font-weight: 600; }
  .contact__division { color: var(--text-muted); }
  .contact--email .contact__lines { color: var(--text-muted); }
</style>
</head>
<body>
<main class="stage">

  <section class="card card--front" aria-label="Business card front">
    <div class="logo-panel"><span class="logo-panel__name">KestrelOak</span></div>

    <div class="contact contact--person">
      <svg class="contact__icon" viewBox="0 0 26 26" aria-hidden="true">
        <rect x="1" y="1" width="24" height="24" fill="none" stroke="var(--icon-line)" stroke-width="1.5"/>
        <circle cx="13" cy="10.5" r="3.2" fill="var(--icon-line)"/>
        <path d="M7.5 19.5c0-3.2 2.5-5 5.5-5s5.5 1.8 5.5 5z" fill="var(--icon-line)"/>
      </svg>
      <div class="contact__lines">
        <div class="contact__name">Marcus Thiel</div>
        <div class="contact__role">Principle Consultant -</div>
        <div class="contact__division">F&amp;B and Hospitality</div>
      </div>
    </div>

    <div class="contact contact--phone">
      <svg class="contact__icon" viewBox="0 0 26 26" aria-hidden="true">
        <rect x="1" y="1" width="24" height="24" fill="none" stroke="var(--icon-line)" stroke-width="1.5"/>
        <path d="M9 7.5l2.2 0.4 0.8 2.8-1.5 1.1c0.8 1.8 2 3 3.7 3.8l1.1-1.5 2.8 0.8 0.4 2.2c-0.6 0.9-1.6 1.4-2.7 1.2-4.2-0.8-7.5-4.1-8.2-8.3-0.2-1.1 0.4-2 1.4-2.5z" fill="var(--icon-line)"/>
      </svg>
      <div class="contact__lines">(+65) 8043 5617</div>
    </div>

    <div class="contact contact--email">
      <svg class="contact__icon" viewBox="0 0 26 26" aria-hidden="true">
        <rect x="1" y="1" width="24" height="24" fill="none" stroke="var(--icon-line)" stroke-width="1.5"/>
        <rect x="7" y="8.5" width="12" height="9" fill="var(--icon-line)"/>
        <path d="M7 8.5l6 5 6-5" fill="none" stroke="var(--card)" stroke-width="1.3"/>
      </svg>
      <div class="contact__lines">marcus@kestreloak.com.sg</div>
    </div>

    <div class="card__stripe"></div>
  </section>

  <section class="card card--back" aria-label="Business card back">
    <div class="logo-panel"><span class="logo-panel__name">KestrelOak</span></div>
    <div class="card__stripe"></div>
  </section>

</main>
</body>
</html>
```